Landscape design build company door flyer

I would like this flyer to convey a high-level of professionalism for a company that is excellent with communication with their clients as well as a company that does incredible installations

Went on vacation/holiday

```html
<!DOCTYPE html>
<html lang="en">
<head>
<meta charset="utf-8">
<title>Cedar Crest Builders – Door Flyer</title>
<link href="https://fonts.googleapis.com/css2?family=Poppins:wght@400;500;600;700;800&family=Oswald:wght@500;600&display=swap" rel="stylesheet">
<style>
  :root{
    --navy:#15304a;
    --navy-deep:#14283a;
    --gold:#f6b100;
    --paper:#f1f1f1;
    --panel:#f2f2f2;
    --ink:#1d2a36;
    --stage:#e9e9e9;
    --white:#ffffff;
  }
  *{box-sizing:border-box;margin:0;padding:0}
  html,body{width:1200px;height:1029px;overflow:hidden;background:var(--stage)}
  body{font-family:"Poppins",sans-serif;color:var(--ink)}

  .flyer{
    position:absolute;left:215px;top:19px;width:770px;height:990px;
    background:var(--paper);overflow:hidden;
    box-shadow:0 6px 24px rgba(0,0,0,.18);
  }

  /* hero */
  .hero-photo{
    position:absolute;left:0;top:0;width:770px;height:538px;
    background:
      radial-gradient(ellipse 200px 260px at 90px 260px,#5d7a32 0%,#47632a 55%,transparent 80%),
      radial-gradient(ellipse 160px 320px at 720px 380px,#2f5a2c 0%,#274a28 60%,transparent 85%),
      radial-gradient(ellipse 160px 130px at 430px 140px,#6f7f8a 0%,#596873 70%,transparent 100%),
      linear-gradient(180deg,#4f5e63 0%,#5f6a6a 35%,#6e6e68 60%,#5a4a3c 100%);
  }
  .logo-panel{position:absolute;left:0;top:0;width:442px;height:168px}
  .brand{
    position:absolute;left:0;top:0;width:355px;height:168px;
    display:flex;align-items:center;justify-content:center;
  }
  .brand-name{
    font-family:"Poppins",sans-serif;font-weight:600;font-size:22px;
    color:var(--navy);letter-spacing:.5px;text-align:center;line-height:1.15;
  }
  .headline{
    position:absolute;right:26px;top:80px;text-align:right;
    font-family:"Poppins",sans-serif;font-weight:800;font-size:45px;
    line-height:37px;letter-spacing:-1px;text-transform:uppercase;
  }
  .headline .line-white{color:var(--white);display:block}
  .headline .line-gold{color:var(--gold);display:block}

  /* project circles */
  .project{
    position:absolute;top:414px;width:206px;height:206px;border-radius:50%;
    border:6px solid var(--white);
  }
  .project--deck{left:44px;background:linear-gradient(180deg,#4e8a3c 0%,#6a9a4a 35%,#8a3e22 60%,#7a3a22 100%)}
  .project--pool{left:282px;background:linear-gradient(180deg,#c9ced3 0%,#8a9a90 35%,#3f6a48 48%,#2fb3a8 62%,#b8c0c4 80%,#d0d4d6 100%)}
  .project--steps{left:520px;background:linear-gradient(180deg,#4a5a30 0%,#6a4a34 25%,#5d6266 45%,#3e4448 75%,#2e3236 100%)}

  /* about */
  .section-title{
    position:absolute;top:656px;font-weight:600;font-size:23px;color:var(--navy);
    letter-spacing:.2px;
  }
  .about-title{left:34px}
  .services-title{left:454px}
  .about-text{
    position:absolute;left:34px;top:700px;width:327px;
    font-size:12px;line-height:14.7px;text-align:justify;color:var(--ink);
  }
  .about-areas{
    position:absolute;left:34px;top:857px;width:327px;
    font-size:12.5px;line-height:16px;font-weight:500;text-align:justify;color:var(--ink);
  }
  .divider{position:absolute;left:408px;top:688px;width:2px;height:168px;background:var(--navy);border-radius:1px}

  /* services */
  .services-list{position:absolute;left:454px;top:697px;list-style:none}
  .services-list li{
    display:flex;align-items:center;height:25.8px;
    font-weight:500;font-size:16.5px;color:var(--ink);
  }
  .services-list svg{width:16px;height:16px;margin-right:18px;flex:none}

  /* contact */
  .contact-cta{
    position:absolute;left:34px;top:921px;font-weight:700;font-size:26px;
    letter-spacing:2.3px;color:var(--gold);line-height:1;
  }
  .contact-links{
    position:absolute;left:34px;top:959px;display:flex;gap:30px;
    font-family:"Oswald",sans-serif;font-weight:500;font-size:11.5px;color:var(--navy);
  }
  .contact-links span{display:flex;align-items:center;gap:6px}
  .contact-links svg{width:11px;height:11px}

  .phone-band{
    position:absolute;left:367px;top:918px;width:403px;height:56px;
    background:var(--navy-deep);display:flex;align-items:center;padding-left:12px;
  }
  .phone-icon{width:22px;height:26px;margin-right:10px}
  .phone-number{
    font-family:"Oswald",sans-serif;font-weight:600;font-size:32px;
    color:var(--gold);letter-spacing:.5px;line-height:1;
  }
  .phone-note{
    font-family:"Oswald",sans-serif;font-weight:500;font-size:19px;
    color:var(--white);margin-left:9px;letter-spacing:-.3px;line-height:1;
  }
</style>
</head>
<body>
<main class="flyer">
  <div class="hero-photo" role="img" aria-label="Aerial photo of a home with a grey paver driveway, walkway, stairs, planting beds and evergreen trees"></div>

  <svg class="logo-panel" viewBox="0 0 442 168" aria-hidden="true">
    <polygon points="0,0 442,0 355,168 0,168" fill="var(--panel)"/>
  </svg>
  <div class="brand"><p class="brand-name">CEDAR CREST<br>BUILDERS</p></div>

  <h1 class="headline">
    <span class="line-white">Let’s create</span>
    <span class="line-white">your dream</span>
    <span class="line-gold">outdoor living</span>
    <span class="line-gold">space!</span>
  </h1>

  <div class="project project--deck" role="img" aria-label="Photo of a stained wood deck with patio chairs and a pergola"></div>
  <div class="project project--pool" role="img" aria-label="Photo of a backyard pool with a stone paver surround"></div>
  <div class="project project--steps" role="img" aria-label="Photo of stone retaining wall steps beside a mulched bed"></div>

  <h2 class="section-title about-title">ABOUT US</h2>
  <p class="about-text">Discover the endless possibilities for your outdoor space with The Cedar Crest Builders Team. Our team of skilled artisans is dedicated to turning your outdoor space into a breathtaking oasis that you’ll love coming home to. Whether it’s a cozy patio for intimate gatherings, a sprawling deck to host memorable parties, or a custom paver driveway that adds instant curb appeal, our high-quality craftsmanship ensures stunning results that exceed your expectations.</p>
  <p class="about-areas">Our service areas include Bellevue, Issaquah, Kirkland, Redmond, Sammamish.</p>

  <div class="divider"></div>

  <h2 class="section-title services-title">OUR SERVICES</h2>
  <ul class="services-list">
    <li><svg viewBox="0 0 16 16"><circle cx="8" cy="8" r="8" fill="var(--navy)"/><path d="M4.4 8.3l2.4 2.3 4.8-4.9" stroke="#fff" stroke-width="1.9" fill="none"/></svg>Paver Patios</li>
    <li><svg viewBox="0 0 16 16"><circle cx="8" cy="8" r="8" fill="var(--navy)"/><path d="M4.4 8.3l2.4 2.3 4.8-4.9" stroke="#fff" stroke-width="1.9" fill="none"/></svg>Paver Driveways</li>
    <li><svg viewBox="0 0 16 16"><circle cx="8" cy="8" r="8" fill="var(--navy)"/><path d="M4.4 8.3l2.4 2.3 4.8-4.9" stroke="#fff" stroke-width="1.9" fill="none"/></svg>Retaining Walls</li>
    <li><svg viewBox="0 0 16 16"><circle cx="8" cy="8" r="8" fill="var(--navy)"/><path d="M4.4 8.3l2.4 2.3 4.8-4.9" stroke="#fff" stroke-width="1.9" fill="none"/></svg>Decks &amp; Railings</li>
    <li><svg viewBox="0 0 16 16"><circle cx="8" cy="8" r="8" fill="var(--navy)"/><path d="M4.4 8.3l2.4 2.3 4.8-4.9" stroke="#fff" stroke-width="1.9" fill="none"/></svg>Pools</li>
    <li><svg viewBox="0 0 16 16"><circle cx="8" cy="8" r="8" fill="var(--navy)"/><path d="M4.4 8.3l2.4 2.3 4.8-4.9" stroke="#fff" stroke-width="1.9" fill="none"/></svg>Outdoor Lighting</li>
    <li><svg viewBox="0 0 16 16"><circle cx="8" cy="8" r="8" fill="var(--navy)"/><path d="M4.4 8.3l2.4 2.3 4.8-4.9" stroke="#fff" stroke-width="1.9" fill="none"/></svg>Firepits &amp; Fireplaces</li>
  </ul>

  <p class="contact-cta">CONTACT US TODAY!</p>
  <div class="contact-links">
    <span><svg viewBox="0 0 12 12"><rect x=".5" y="2" width="11" height="8" fill="var(--gold)"/><path d="M.5 2l5.5 4.5L11.5 2" stroke="#fff" stroke-width="1" fill="none"/></svg>www.cedarcrestbuilders.com</span>
    <span><svg viewBox="0 0 12 12" fill="none" stroke="var(--gold)" stroke-width="1"><circle cx="6" cy="6" r="5.3"/><ellipse cx="6" cy="6" rx="2.3" ry="5.3"/><path d="M.7 6h10.6M1.6 3.3h8.8M1.6 8.7h8.8"/></svg>info@cedarcrestbuilders.com</span>
  </div>

  <div class="phone-band">
    <svg class="phone-icon" viewBox="0 0 22 26" aria-hidden="true">
      <rect width="22" height="26" rx="2" fill="var(--gold)"/>
      <path d="M7 5.5c-1.3.4-2.2 1.5-2 3 .5 4.5 3.6 9.3 7.8 11.6 1.3.7 2.7.3 3.5-.8l.6-.9-3-2.3-1.3 1.3c-1.9-1.1-3.4-3.4-4-5.6l1.6-.9L9 6z" fill="var(--navy-deep)"/>
    </svg>
    <span class="phone-number">206-555-0148</span>
    <span class="phone-note">FOR FREE ESTIMATE</span>
  </div>
</main>
</body>
</html>
```